Thornvale Group needs a business card design

We need a new business card design using the logo recently selected in a logo competition on Pixel Bazaar. Our business is a consultancy specializing in aviation and energy and the winning business card design will promote an image of precision and professionalism with creativity.

Please use the logo with the name on the front of the card and use a complementary font. Make the back white with either the light grey or dark grey logo.

Target Market(s)

Senior finance and legal leaders at aviation and energy companies

Industry/Entity Type

Management Consulting

Contact Information for Business Card

Peter Castrell
President
Thornvale Group

www.thornvalegroup.example

(555) 204-6391
pc@thornvalegroup.example

Requirements
Must have
• Professional font that goes well with the logo font

```html
<!DOCTYPE html>
<html lang="en">
<head>
<meta charset="utf-8">
<title>Thornvale Group — Business Card</title>
<link href="https://fonts.googleapis.com/css2?family=Open+Sans:wght@400;600;700&display=swap" rel="stylesheet">
<style>
  :root {
    --backdrop: #141414;
    --card: #ffffff;
    --navy: #1c3464;
    --grey: #555a60;
  }
  * { margin: 0; padding: 0; box-sizing: border-box; }
  html, body {
    width: 1200px;
    height: 900px;
    overflow: hidden;
    background: var(--backdrop);
    font-family: "Open Sans", sans-serif;
  }
  .stage { position: relative; width: 1200px; height: 900px; }
  .card {
    position: absolute;
    top: 306px;
    width: 440px;
    height: 271px;
    background: var(--card);
    border-radius: 10px;
  }
  .card--front { left: 149px; }
  .card--back { left: 608px; }

  .wordmark {
    position: absolute;
    color: var(--navy);
    font-weight: 400;
    text-align: center;
    text-transform: uppercase;
    line-height: 1;
  }
  .wordmark span { display: block; }
  .card--front .wordmark { left: 24px; top: 150px; width: 182px; }
  .card--front .wordmark .wordmark-name { font-size: 23px; letter-spacing: 0.5px; }
  .card--front .wordmark .wordmark-group { font-size: 11px; letter-spacing: 13px; margin-top: 7px; padding-left: 13px; }

  .contact { position: absolute; left: 243px; top: 92px; }
  .contact-name { color: var(--navy); font-size: 15px; font-weight: 600; line-height: 20px; }
  .contact-role { color: var(--grey); font-size: 12px; line-height: 15px; }
  .contact-list { list-style: none; margin-top: 20px; }
  .contact-list li {
    display: flex; align-items: center; gap: 7px;
    color: var(--grey); font-size: 12px; line-height: 16px;
  }
  .contact-list svg { width: 10px; height: 10px; flex: none; fill: var(--navy); }

  .card--back .wordmark { left: 0; top: 103px; width: 100%; }
  .card--back .wordmark .wordmark-name { font-size: 38px; letter-spacing: 1px; }
  .card--back .wordmark .wordmark-group { font-size: 18px; letter-spacing: 30px; margin-top: 10px; padding-left: 30px; }
  .tagline { position: absolute; left: 0; top: 197px; width: 100%; text-align: center; }
  .tagline-service { color: var(--navy); font-size: 13px; font-weight: 700; letter-spacing: -0.3px; line-height: 18px; }
  .tagline-sectors { color: var(--grey); font-size: 13px; letter-spacing: -0.3px; line-height: 22px; }
</style>
</head>
<body>
<main class="stage">
  <section class="card card--front" aria-label="Card front">
    <div class="wordmark">
      <span class="wordmark-name">Thornvale</span>
      <span class="wordmark-group">Group</span>
    </div>
    <div class="contact">
      <p class="contact-name">Peter J. Castrell</p>
      <p class="contact-role">President</p>
      <ul class="contact-list">
        <li>
          <svg viewBox="0 0 10 10" aria-hidden="true"><path d="M2.1 0.4 3.6 2.4 2.7 3.5C3.3 4.8 4.6 6.2 6.1 6.9L7.3 6 9.6 7.5 8.9 9.2C4.6 9.4 0.6 5.4 0.6 1.1Z"/></svg>
          (555) 204-6391
        </li>
        <li>
          <svg viewBox="0 0 10 10" aria-hidden="true"><path d="M0.5 2H9.5V8.5H0.5Z M1.2 2.6 5 5.6 8.8 2.6" stroke="#fff" stroke-width="0.8"/></svg>
          pc@thornvalegroup.example
        </li>
      </ul>
    </div>
  </section>

  <section class="card card--back" aria-label="Card back">
    <div class="wordmark">
      <span class="wordmark-name">Thornvale</span>
      <span class="wordmark-group">Group</span>
    </div>
    <div class="tagline">
      <p class="tagline-service">Finance and Strategy Consulting</p>
      <p class="tagline-sectors">Aviation - Manufacturing - Energy</p>
    </div>
  </section>
</main>
</body>
</html>
```